Bramblewood Joinery Website

My client Bramblewood Joinery is looking for a redesign for a Word Press Website. Their current site is at www.bramblewoodjoinery.example They are a custom cabinet company, but also create bathroom, living room, bar and entertainment and bedroom cabinets too. They would like a design that emulates the master craftsman work they do yet a contemporary style.

Their current site was designed using Flash elements.

Target Market(s)

Home owners and builders of high end homes

Industry/Entity Type

Entertainment

Font styles to use
Serif
Decorative

Requirements
Must have
• Must show their work and logo using a contemporary style.
Nice to have
• Sliders that showcase their projects.

```html
<!DOCTYPE html>
<html lang="en">
<head>
<meta charset="utf-8">
<title>Bramblewood Joinery</title>
<link href="https://fonts.googleapis.com/css2?family=Crimson+Text:wght@400;600&family=Open+Sans:ital,wght@0,400;0,600;1,400;1,600&display=swap" rel="stylesheet">
<style>
:root{
  --green:#3fae3f;
  --green-dark:#2f9a35;
  --green-soft:#e9f4e6;
  --ink:#333;
  --muted:#777;
  --line:#d6e2d2;
  --footer:#d9d9d9;
}
*{margin:0;padding:0;box-sizing:border-box}
html,body{width:814px;height:1200px;overflow:hidden}
body{position:relative;font-family:"Open Sans",Arial,sans-serif;color:var(--ink);
  background:linear-gradient(#fff 0,#fff 90px,#eaf5e6 480px,#eef6ec 620px,#f4f9f2 900px,#fff 1050px)}
.abs{position:absolute}
.logo{left:74px;top:10px;display:flex;align-items:center;gap:6px}
.logo-dot{width:20px;height:20px;border-radius:50%;background:var(--green)}
.logo-name{font-family:"Crimson Text",Georgia,serif;font-weight:600;font-size:16px;color:var(--ink);line-height:1;width:120px}
.util-nav{right:74px;top:26px;display:flex;align-items:baseline;gap:17px;font-style:italic;font-size:10px;color:#999}
.util-nav .call{font-weight:600;font-size:12px;color:var(--ink);display:flex;align-items:center;gap:4px}
.util-nav .call b{color:var(--green);font-weight:600}
.main-nav{right:74px;top:54px;display:flex;align-items:center;gap:24px;font-style:italic;font-size:10px;color:#444;font-weight:600}
.main-nav .active{background:var(--green);color:#fff;padding:4px 11px}
.hero{left:74px;top:98px;width:666px;height:382px;overflow:hidden}
.hero-photo{position:absolute;inset:0;background:linear-gradient(100deg,#d9b27c 0%,#f1e2c3 35%,#e6d0a8 60%,#b88454 100%)}
.hero svg{position:absolute;inset:0}
.service{position:absolute;color:#fff;font-size:9.5px;line-height:12px;width:134px}
.service h3{font-weight:400;font-size:15px;line-height:18px;margin-bottom:2px;white-space:nowrap}
.hero-shadow{left:110px;top:478px;width:594px;height:14px;border-radius:50%;background:radial-gradient(ellipse at center,rgba(0,0,0,.22),rgba(0,0,0,0) 70%)}
.serif{font-family:"Crimson Text",Georgia,serif}
.green{color:var(--green)}
.welcome{left:0;width:814px;top:510px;text-align:center;font-size:20px;font-weight:400}
.intro{left:134px;width:546px;top:546px;text-align:center;font-size:9px;line-height:14px;color:var(--muted)}
.features{left:0;top:611px;width:814px;height:232px;border-top:1px dashed #c9d8c5;display:flex}
.feature{text-align:center;padding-top:26px;border-bottom:1px solid #dfe9dc}
.feature.hi{background:#e0eddc;border-left:1px solid #d3e1cf;border-right:1px solid #d3e1cf}
.feature-img{margin:0 auto;width:170px;height:110px;border-radius:4px}
.feature h4{font-family:"Crimson Text",Georgia,serif;font-weight:400;font-size:14px;color:var(--green);margin-top:17px;letter-spacing:.3px}
.feature p{font-size:10px;line-height:14px;color:var(--muted);width:200px;margin:3px auto 0}
.about-head{left:116px;top:853px;font-size:20px;font-weight:400}
.about-rule{left:116px;top:885px;width:624px;height:1px;background:#cfd9cc}
.about-text{left:116px;top:894px;width:410px;font-size:9.2px;line-height:13.6px;color:var(--muted)}
.about-text p{margin-bottom:9px}
.btn-more{left:116px;top:994px;width:130px;height:24px;border:1px solid #a9d3a3;border-radius:12px;background:linear-gradient(#fff,#e3f1df);font-size:10px;font-weight:600;text-align:center;line-height:22px}
.video{left:536px;top:897px;width:204px;height:120px;background:linear-gradient(120deg,#3e3127,#7a5a3c 50%,#2d2a26)}
.foot-nav{left:0;top:1050px;width:814px;height:38px;border-top:2px solid #777;background:#fff}
.foot-nav ul{list-style:none;display:flex;gap:18px;margin-left:74px;margin-top:11px;font-size:10px;color:#444}
.foot-nav .mark{position:absolute;left:84px;top:0;width:0;height:0;border-left:4px solid transparent;border-right:4px solid transparent;border-top:5px solid #666}
.footer{left:0;top:1088px;width:814px;height:112px;background:var(--footer)}
.social{left:135px;top:1127px;display:flex;gap:5px}
.social span{width:22px;height:22px;border-radius:3px}
.copy{left:74px;top:1158px;width:240px;font-size:9px;line-height:12px;color:#444}
.news-title{left:336px;top:1109px;font-size:12px;color:#555}
.news-sub{left:338px;top:1127px;font-size:8.5px;color:#555}
.news-form{left:338px;top:1150px;width:186px;height:24px;background:#fff;border:1px solid #ccc;display:flex;align-items:center}
.news-form .label{background:var(--green);color:#fff;font-size:10px;font-weight:600;width:52px;height:100%;display:flex;align-items:center;justify-content:center}
.news-form svg{margin-left:auto;margin-right:6px}
.address{left:565px;top:1099px;font-size:8.5px;line-height:13.5px;color:#444}
.contact-btn{left:566px;top:1150px;height:24px;display:flex;gap:2px}
.contact-btn .ico{width:33px;background:var(--green);display:flex;align-items:center;justify-content:center}
.contact-btn .txt{width:139px;background:var(--green);color:#fff;font-size:12px;font-weight:600;display:flex;align-items:center;justify-content:center}
</style>
</head>
<body>

<div class="abs logo"><span class="logo-dot"></span><span class="logo-name">Bramblewood Joinery</span></div>

<nav class="abs util-nav">
  <span>Professional</span><span>Portfolio</span><span>Cabinet Hardware</span>
  <span class="call"><svg width="10" height="10" viewBox="0 0 24 24"><path fill="#333" d="M6.6 10.8a15 15 0 0 0 6.6 6.6l2.2-2.2a1 1 0 0 1 1-.25 11 11 0 0 0 3.6.6 1 1 0 0 1 1 1V20a1 1 0 0 1-1 1A17 17 0 0 1 3 4a1 1 0 0 1 1-1h3.5a1 1 0 0 1 1 1c0 1.250.2 2.45.6 3.6a1 1 0 0 1-.25 1z"/></svg>Call Today..! <b>1-800-555-0142</b></span>
</nav>
<nav class="abs main-nav">
  <span class="active">Home</span><span>Who We Are</span><span>Getting Started</span><span>Contact Us</span><span>Customer Experience</span>
</nav>

<section class="abs hero">
  <div class="hero-photo" role="img" aria-label="Photo of a cream child's bedroom with built-in shelving, toys and a daybed"></div>
  <svg width="666" height="382" viewBox="0 0 666 382">
    <path d="M518 0 C455 70 408 170 420 245 C430 305 485 350 518 382 L666 382 L666 0Z" fill="#3fae3f" opacity=".92"/>
    <path d="M518 0 C455 70 408 170 420 245 C430 305 485 350 518 382" fill="none" stroke="#2f9a35" stroke-width="4"/>
    <g stroke="#fff" stroke-width="3" opacity=".95">
      <polygon points="470,58 504,74 504,112 470,128 436,112 436,74" fill="#d9c4a0" role="img" aria-label="Home interior photo"/>
      <polygon points="412,196 452,160 490,196 452,234" fill="#b06a34" role="img" aria-label="Kitchen photo"/>
      <polygon points="478,256 508,284 500,330 458,338 432,300 448,266" fill="#c9b9a3" role="img" aria-label="Bathroom photo"/>
    </g>
  </svg>
  <div class="service" style="left:513px;top:64px"><h3>Home Services</h3>Lorem ipsum dolor sit amet, consectetur adipiscing elit, sed do euismod tempor</div>
  <div class="service" style="left:511px;top:159px"><h3>Kitchen Services</h3>Lorem ipsum dolor sit amet, consectetur adipiscing elit, sed do euismod tempor</div>
  <div class="service" style="left:516px;top:250px"><h3>Bathroom Services</h3>Lorem ipsum dolor sit amet, consectetur adipiscing elit, sed do euismod tempor</div>
</section>
<div class="abs hero-shadow"></div>

<h1 class="abs welcome serif">Welcome To <span class="green">BRAMBLEWOOD</span> Cabinet &amp; Fixtures</h1>
<p class="abs intro">Lorem ipsum dolor sit amet, consectetur adipiscing elit, sed do eiusmod tempor incididunt ut labore et dolore magna aliqua. Ut enim ad minim veniam, quis nostrud exercitation ullamco laboris nisi ut aliquip ex ea commodo consequat ut enim ad minim orem ipsum dolor sit amet, consectetur adipiscing elit..</p>

<section class="abs features">
  <div class="feature" style="width:291px">
    <div class="feature-img" role="img" aria-label="Wooden kitchen cabinet set" style="background:linear-gradient(#eef3ec,#c98a4e 40%,#b67940)"></div>
    <h4>KITCHENS</h4><p>Our cabinets come fully loaded! While other cabinet companies charge for...</p>
  </div>
  <div class="feature hi" style="width:232px">
    <div class="feature-img" role="img" aria-label="Kitchen design sketch" style="background:linear-gradient(135deg,#e4ebe2,#b9c4bc 50%,#e0e8de)"></div>
    <h4>DESIGN SERVICES</h4><p>Our cabinets come fully loaded! While other cabinet companies charge for...</p>
  </div>
  <div class="feature" style="width:291px">
    <div class="feature-img" role="img" aria-label="Installers fitting a kitchen" style="background:linear-gradient(#f0ead8,#c9a57a 60%,#a88560)"></div>
    <h4>KITCHENS</h4><p>Our cabinets come fully loaded! While other cabinet companies charge for...</p>
  </div>
</section>

<svg class="abs" style="left:74px;top:843px" width="34" height="51" viewBox="0 0 34 51"><path d="M0 0H34V51L17 41L0 51Z" fill="#3fae3f"/></svg>
<h2 class="abs about-head serif">About <span class="green">BRAMBLEWOOD</span> Cabinet &amp; Fixtures</h2>
<div class="abs about-rule"></div>
<div class="abs about-text">
  <p>Lorem ipsum dolor sit amet, consectetur adipiscing elit, sed do eiusmod tempor incididunt ut labore et dolore magna aliqua. Ut enim ad minim veniam, quis nostrud exercitation ullamco laboris nisi ut aliquip ex ea commodo consequat.</p>
  <p>Ut enim ad minim orem ipsum dolor sit amet, consectetur adipiscing elit, sed do eiusmod tempor incididunt ut labore et dolore magna aliqua. Ut enim ad minim veniam, quis nostrud exercitation ullamco laboris nisi ut aliquip ex ea commodo consequat.</p>
</div>
<div class="abs btn-more">Continue Reading...</div>
<div class="abs video" role="img" aria-label="Video still of a finished wooden kitchen">
  <svg width="204" height="120" viewBox="0 0 204 120"><circle cx="102" cy="60" r="27" fill="none" stroke="rgba(255,255,255,.5)" stroke-width="4"/><path d="M95 48L113 60L95 72Z" fill="rgba(255,255,255,.5)"/></svg>
</div>

<nav class="abs foot-nav"><span class="mark"></span>
  <ul><li>Home</li><li>Who We Are</li><li>Getting Started</li><li>Contact Us</li><li>Customer Experience</li><li>Professional</li><li>Portfolio</li><li>Cabinet Hardware</li></ul>
</nav>

<footer class="abs footer"></footer>
<div class="abs social"><span style="background:#3b5a9a"></span><span style="background:#333"></span><span style="background:#c4262e"></span><span style="background:#3fa9d9"></span></div>
<div class="abs copy">Copyrights © 2015 bramblewoodjoinery.example<br>All Rights Reserved</div>
<div class="abs news-title">Newsletter</div>
<div class="abs news-sub">Join us to start receiving news about new</div>
<div class="abs news-form"><span class="label">Email</span>
  <svg width="16" height="16" viewBox="0 0 16 16"><circle cx="8" cy="8" r="7" fill="none" stroke="#666" stroke-width="1.4"/><path d="M4 8H11M8 5L11 8L8 11" fill="none" stroke="#666" stroke-width="1.4"/></svg>
</div>
<div class="abs address">Service Centers<br>5678 Elm Row, Suite 210 - 318<br>Riverton 5678</div>
<div class="abs contact-btn">
  <span class="ico"><svg width="12" height="12" viewBox="0 0 24 24"><path fill="#fff" d="M6.6 10.8a15 15 0 0 0 6.6 6.6l2.2-2.2a1 1 0 0 1 1-.25 11 11 0 0 0 3.6.6 1 1 0 0 1 1 1V20a1 1 0 0 1-1 1A17 17 0 0 1 3 4a1 1 0 0 1 1-1h3.5a1 1 0 0 1 1 1c0 1.25.2 2.45.6 3.6a1 1 0 0 1-.25 1z"/></svg></span>
  <span class="txt">Contact Us Today..!</span>
</div>

</body>
</html>
```